Business Cards Design for the electrical wholesaler: clean bold dynamic :)

We need a business card design that would follow our latest brand guidelines. As an electrical wholesaler we want to bring a fresh look and feel into the industry. The design should be clean bold and dynamic. It should come alive with the renewed energy of our green colour. Our grey colour should keep things balanced and complement the notion of maturity and responsibility. We employ Lato as a corporate font however are not bound by this font and we’re open to interpretation here.

Target Market(s)

Electrical contractors

Industry/Entity Type

Business

Contact Information for Business Card

Logo
Name & Surname: Halyna Dorosh
Job Title: Director of Marketing
Email: halya.dorosh@quillmail.example
Cell phone: XXX.XXX.XXXX
Address: 20517 - 87 Ave. Edmonton, AB, Canada. T6K 4N8
Business Phone: 780.555.0184
Website: www.brovix.example

Font styles to use
Other font styles liked:
• Lato

Requirements
Must have
• Logo & website
Nice to have
• Brand elements - some of them you may find in the attached Brand Guidelines (e.g. three lines on the background signifying "W")

```html
<!DOCTYPE html>
<html lang="en">
<head>
<meta charset="utf-8">
<title>Brovix Business Cards</title>
<link href="https://fonts.googleapis.com/css2?family=Lato:wght@400;700&display=swap" rel="stylesheet">
<style>
  :root {
    --brand-green: #8dc63f;
    --brand-grey: #58595b;
    --text-grey: #555659;
    --rule-grey: #6d6e70;
    --paper: #ffffff;
    --backdrop: #dfe3e8;
  }
  * { box-sizing: border-box; margin: 0; padding: 0; }
  html, body { width: 1200px; height: 1000px; overflow: hidden; }
  body {
    background: var(--backdrop);
    font-family: "Lato", Arial, sans-serif;
    position: relative;
  }
  .card { position: absolute; overflow: hidden; }
  .card--rounded { width: 508px; height: 290px; border-radius: 26px; }
  .card--square { width: 513px; height: 293px; }
  .front-rounded { left: 64px; top: 60px; }
  .back-rounded { left: 64px; top: 427px; }
  .front-square { left: 624px; top: 283px; }
  .back-square { left: 624px; top: 639px; }

  .card-front { background: var(--brand-green); }
  .card-front .wave { position: absolute; left: 0; bottom: 0; width: 100%; height: 100%; }
  .wordmark {
    display: flex; align-items: center; gap: 10px;
    color: var(--brand-grey); font-weight: 700; letter-spacing: -1px; line-height: 1;
  }
  .wordmark__dot { background: var(--brand-grey); border-radius: 50%; }
  .card-front .wordmark {
    position: absolute; left: 0; right: 0; top: 92px; justify-content: center;
    font-size: 58px;
  }
  .card-front .wordmark__dot { width: 40px; height: 40px; }

  .card-back { background: var(--paper); color: var(--text-grey); }
  .card-back .wordmark { position: absolute; right: 30px; top: 26px; font-size: 44px; }
  .card-back .wordmark__dot { width: 30px; height: 30px; background: var(--brand-green); }
  .person { position: absolute; left: 27px; top: 94px; right: 30px; }
  .person__name { font-size: 25px; font-weight: 400; }
  .person__role { display: flex; align-items: center; gap: 8px; font-size: 15px; margin-top: 4px; }
  .person__rule { flex: 1; height: 2px; background: var(--rule-grey); margin-top: 8px; }
  .address {
    position: absolute; right: 30px; top: 150px; text-align: right;
    font-size: 15.5px; line-height: 20px;
  }
  .address__pin { width: 11px; height: 14px; margin-right: 6px; vertical-align: -1px; }
  .contacts { position: absolute; left: 28px; top: 183px; list-style: none; font-size: 17px; line-height: 24px; }
  .contacts li { display: flex; align-items: center; gap: 11px; }
  .contacts svg { width: 13px; height: 13px; fill: var(--text-grey); }
  .website { position: absolute; right: 30px; top: 244px; font-size: 15px; }
</style>
</head>
<body>

<!-- Front, rounded -->
<section class="card card--rounded card-front front-rounded">
  <svg class="wave" viewBox="0 0 508 290" preserveAspectRatio="none">
    <path d="M0,240 C60,270 140,276 230,252 S420,188 508,218 L508,290 L0,290 Z" fill="var(--brand-grey)"/>
    <path d="M0,240 C60,270 140,276 230,252 S420,188 508,218" fill="none" stroke="#fff" stroke-width="3"/>
  </svg>
  <div class="wordmark"><span class="wordmark__dot"></span>brovix</div>
</section>

<!-- Back, rounded -->
<section class="card card--rounded card-back back-rounded">
  <div class="wordmark"><span class="wordmark__dot"></span>brovix</div>
  <div class="person">
    <h1 class="person__name">Halyna Dorosh</h1>
    <p class="person__role">Director of Marketing <span class="person__rule"></span></p>
  </div>
  <p class="address">
    <svg class="address__pin" viewBox="0 0 12 16"><path d="M6 0C2.7 0 0 2.6 0 5.9 0 10 6 16 6 16s6-6 6-10.1C12 2.6 9.3 0 6 0zm0 8.2A2.3 2.3 0 1 1 6 3.6a2.3 2.3 0 0 1 0 4.6z" fill="var(--text-grey)"/></svg>20517 - 87 Ave. Edmonton<br>AB, Canada. T6K 4N8
  </p>
  <ul class="contacts">
    <li><svg viewBox="0 0 16 16"><path d="M3.6 0l3 3.6-1.8 2c.9 2 2.5 3.7 4.6 4.6l2-1.8L15 11.4 13.4 15C6.6 15 1 9.4 1 2.6z"/></svg>780.555.0184</li>
    <li><svg viewBox="0 0 16 16"><path d="M1 5c0-2 3-3 7-3s7 1 7 3v1h-3.5V4.5h-7V6H1zm3 2h8l2 3v4H2v-4zm4 1.5a2 2 0 1 0 0 4 2 2 0 0 0 0-4z"/></svg>780.555.0184</li>
    <li><svg viewBox="0 0 16 16"><path d="M1 3h14v1.5L8 9 1 4.5zm0 3.2l7 4.5 7-4.5V13H1z"/></svg>halya.dorosh@quillmail.example</li>
  </ul>
  <p class="website">www.brovix.example</p>
</section>

<!-- Front, square -->
<section class="card card--square card-front front-square">
  <svg class="wave" viewBox="0 0 513 293" preserveAspectRatio="none">
    <path d="M0,243 C60,273 140,279 232,255 S424,190 513,220 L513,293 L0,293 Z" fill="var(--brand-grey)"/>
    <path d="M0,243 C60,273 140,279 232,255 S424,190 513,220" fill="none" stroke="#fff" stroke-width="3"/>
  </svg>
  <div class="wordmark"><span class="wordmark__dot"></span>brovix</div>
</section>

<!-- Back, square -->
<section class="card card--square card-back back-square">
  <div class="wordmark"><span class="wordmark__dot"></span>brovix</div>
  <div class="person">
    <h2 class="person__name">Halyna Dorosh</h2>
    <p class="person__role">Director of Marketing <span class="person__rule"></span></p>
  </div>
  <p class="address">
    <svg class="address__pin" viewBox="0 0 12 16"><path d="M6 0C2.7 0 0 2.6 0 5.9 0 10 6 16 6 16s6-6 6-10.1C12 2.6 9.3 0 6 0zm0 8.2A2.3 2.3 0 1 1 6 3.6a2.3 2.3 0 0 1 0 4.6z" fill="var(--text-grey)"/></svg>20517 - 87 Ave. Edmonton<br>AB, Canada. T6K 4N8
  </p>
  <ul class="contacts">
    <li><svg viewBox="0 0 16 16"><path d="M3.6 0l3 3.6-1.8 2c.9 2 2.5 3.7 4.6 4.6l2-1.8L15 11.4 13.4 15C6.6 15 1 9.4 1 2.6z"/></svg>780.555.0184</li>
    <li><svg viewBox="0 0 16 16"><path d="M1 5c0-2 3-3 7-3s7 1 7 3v1h-3.5V4.5h-7V6H1zm3 2h8l2 3v4H2v-4zm4 1.5a2 2 0 1 0 0 4 2 2 0 0 0 0-4z"/></svg>780.555.0184</li>
    <li><svg viewBox="0 0 16 16"><path d="M1 3h14v1.5L8 9 1 4.5zm0 3.2l7 4.5 7-4.5V13H1z"/></svg>halya.dorosh@quillmail.example</li>
  </ul>
  <p class="website">www.brovix.example</p>
</section>

</body>
</html>
```